Car Dealership Showroom Poster

Design a 3'x5' poster (portiat layout) to advertise our 36 month / 36,000 mile warranty.

Below is a link to our website for color / logo and program details.

https://brockwayautogroupnj.com/

https://brockwayautogroupnj.com/36-month-36000-mile-limited-warranty

https://brockwayautogroupnj.com/36-month-36000-mile-limited-warranty/

```html
<!DOCTYPE html>
<html lang="en">
<head>
<meta charset="utf-8">
<title>Brockway Auto Group – 36 Month / 36,000 Mile Limited Warranty</title>
<link rel="stylesheet" href="https://fonts.googleapis.com/css2?family=Barlow+Condensed:wght@800&family=Poppins:wght@600;700;800&display=swap">
<style>
  :root {
    --mat-green: #04351d;
    --brand-green: #074a25;
    --band-green: #0a4b27;
    --gold: #c99b38;
    --gold-light: #e4c46a;
    --ink: #06341c;
    --white: #ffffff;
  }
  * { box-sizing: border-box; margin: 0; padding: 0; }
  html, body { width: 876px; height: 1200px; overflow: hidden; }
  body { background: var(--mat-green); position: relative; }

  .poster {
    position: absolute; left: 125px; top: 78px;
    width: 626px; height: 1044px;
    background: var(--white); overflow: hidden;
  }

  .scenery {
    position: absolute; left: 0; top: 470px; width: 100%; height: 531px;
    background:
      linear-gradient(180deg, rgba(255,255,255,1) 0%, rgba(255,255,255,0) 30%),
      linear-gradient(180deg, #fbeee2 0%, #f1dccd 26%, #c9b1b0 38%, #b79a86 44%, #8d6f6c 52%, #6d5a5f 64%, #5f5157 80%, #564a50 100%);
  }

  .headline {
    position: absolute; left: 69px; top: 54px;
    font-family: "Barlow Condensed", "Arial Narrow", sans-serif;
    font-weight: 800; font-size: 98px; line-height: 89px;
    text-transform: uppercase; letter-spacing: -0.5px;
  }
  .headline .term { color: var(--gold); display: block; }
  .headline .kind { color: var(--brand-green); display: block; }

  .benefits {
    position: absolute; left: 70px; top: 420px; list-style: none;
    font-family: "Poppins", Arial, sans-serif; font-weight: 700;
    font-size: 19px; color: var(--ink);
  }
  .benefits li { display: flex; align-items: center; height: 32px; }
  .benefits svg { width: 22px; height: 22px; margin-right: 22px; flex: none; }

  .seal {
    position: absolute; left: 72px; top: 609px; width: 210px; height: 210px;
  }

  .brand-name {
    position: absolute; left: 384px; top: 902px; width: 200px;
    font-family: "Poppins", Arial, sans-serif; font-weight: 800;
    color: var(--white); text-align: right; line-height: 1;
  }
  .brand-name .main { display: block; font-size: 33px; letter-spacing: 0.5px; }
  .brand-name .sub { display: block; font-size: 19px; letter-spacing: 4px; margin-top: 4px; }

  .web-band {
    position: absolute; left: 0; bottom: 0; width: 100%; height: 43px;
    background: var(--band-green);
    display: flex; align-items: center; justify-content: center;
    font-family: "Poppins", Arial, sans-serif; font-weight: 700;
    font-size: 15px; letter-spacing: 3px; color: var(--white);
  }
</style>
</head>
<body>
  <main class="poster">
    <div class="scenery" role="img" aria-label="Photograph of an open coastal road stretching toward a hazy mountain at sunrise"></div>

    <h1 class="headline">
      <span class="term">36 Month/</span>
      <span class="term">36,000 Mile</span>
      <span class="kind">Limited</span>
      <span class="kind">Warranty</span>
    </h1>

    <ul class="benefits">
      <li><svg viewBox="0 0 24 24" aria-hidden="true"><circle cx="11" cy="13" r="9" fill="none" stroke="#c99b38" stroke-width="2"/><path d="M6.5 12.5l4 4L22 3" fill="none" stroke="#c99b38" stroke-width="2.4" stroke-linecap="round" stroke-linejoin="round"/></svg>No additional cost to you</li>
      <li><svg viewBox="0 0 24 24" aria-hidden="true"><circle cx="11" cy="13" r="9" fill="none" stroke="#c99b38" stroke-width="2"/><path d="M6.5 12.5l4 4L22 3" fill="none" stroke="#c99b38" stroke-width="2.4" stroke-linecap="round" stroke-linejoin="round"/></svg>In-depth quality inspections</li>
      <li><svg viewBox="0 0 24 24" aria-hidden="true"><circle cx="11" cy="13" r="9" fill="none" stroke="#c99b38" stroke-width="2"/><path d="M6.5 12.5l4 4L22 3" fill="none" stroke="#c99b38" stroke-width="2.4" stroke-linecap="round" stroke-linejoin="round"/></svg>Engine &amp; Powertrain Coverage</li>
      <li><svg viewBox="0 0 24 24" aria-hidden="true"><circle cx="11" cy="13" r="9" fill="none" stroke="#c99b38" stroke-width="2"/><path d="M6.5 12.5l4 4L22 3" fill="none" stroke="#c99b38" stroke-width="2.4" stroke-linecap="round" stroke-linejoin="round"/></svg>Roadside Assistance</li>
      <li><svg viewBox="0 0 24 24" aria-hidden="true"><circle cx="11" cy="13" r="9" fill="none" stroke="#c99b38" stroke-width="2"/><path d="M6.5 12.5l4 4L22 3" fill="none" stroke="#c99b38" stroke-width="2.4" stroke-linecap="round" stroke-linejoin="round"/></svg>Nationwide Service Network</li>
    </ul>

    <svg class="seal" viewBox="0 0 210 210" role="img" aria-label="Warranty seal">
      <circle cx="105" cy="105" r="100" fill="#d6ad4e"/>
      <circle cx="105" cy="105" r="86" fill="#0b7a3c"/>
    </svg>

    <p class="brand-name"><span class="main">BROCKWAY</span><span class="sub">AUTO GROUP</span></p>

    <footer class="web-band">WWW.BROCKWAYAUTOGROUPNJ.COM</footer>
  </main>
</body>
</html>
```